New Business Card for our Indoor Golf Training Facility

We are looking for designs for a new business card for our indoor golf training facility. Attached is our logo, our logo with our slogan, and here is our elevator pitch (What makes us different from the others) not sure if all the info will fit on one card, maybe you can condense the elevator pitch? here is the info

Elevator Pitch
We work with serious golfers and those that want to be serious golfers…
to make you better, faster, at all phases of the game…
We use the same state-of-the-art technology as professional golfers…
which produces data sets that shows your improvement in real time.
Our facility is available 24/7 to our members, which allows you to improve on your time.

our website: www.birchpinlinks.com

Target Market(s)

Golfers

Font styles to use
Serif
Sans Serif

Colors
ec1f27
f59195
fbd4d5
919191
d3d3d3
1b1b1b

Requirements
Must have
• our logo or our logo with the slogan, elevator pitch (can be condensed or shortened)

```html
<!DOCTYPE html>
<html lang="en">
<head>
<meta charset="utf-8">
<title>Birch Pin Links – Business Card</title>
<link href="https://fonts.googleapis.com/css2?family=Open+Sans:wght@400;600;700&display=swap" rel="stylesheet">
<style>
  :root {
    --red: #ec1f27;
    --card: #1b1b1b;
    --ink: #ffffff;
    --muted: #d3d3d3;
    --rule: #4a4a4a;
    --stage: #2c2c2c;
  }
  * { box-sizing: border-box; margin: 0; padding: 0; }
  html, body { width: 1200px; height: 1108px; overflow: hidden; }
  body {
    background: var(--stage);
    font-family: "Open Sans", Arial, sans-serif;
    display: flex;
    align-items: center;
    justify-content: center;
    gap: 60px;
  }
  .card {
    position: relative;
    width: 400px;
    height: 680px;
    background: var(--card);
    border-radius: 22px;
    overflow: hidden;
    color: var(--muted);
    text-align: center;
  }

  /* Front */
  .brand {
    position: absolute;
    top: 150px;
    left: 0; right: 0;
    display: flex;
    flex-direction: column;
    align-items: center;
  }
  .brand-name {
    color: var(--red);
    font-weight: 700;
    font-size: 38px;
    line-height: 1.1;
  }
  .brand-tagline {
    margin-top: 6px;
    color: var(--red);
    font-size: 13px;
    font-weight: 700;
  }
  .contact {
    position: absolute;
    top: 390px;
    left: 0; right: 0;
    display: flex;
    flex-direction: column;
    align-items: center;
  }
  .person-name { color: var(--red); font-size: 30px; font-weight: 600; line-height: 1.1; }
  .person-role { font-size: 18px; margin-top: 2px; }
  .contact .rule { width: 160px; height: 1px; background: var(--rule); margin: 14px 0; }
  .contact p { font-size: 18px; line-height: 1.4; }

  /* Back */
  .pattern-field {
    position: absolute;
    inset: 0;
    background: linear-gradient(180deg, #242424 0%, #1e1e1e 55%, var(--card) 100%);
  }
  .pitch {
    position: relative;
    padding: 130px 34px 0;
    color: var(--ink);
  }
  .pitch h2 { font-size: 22px; font-weight: 700; letter-spacing: 0.5px; margin-bottom: 16px; }
  .pitch p { font-size: 17px; line-height: 1.3; margin-bottom: 16px; }
  .pitch .rule { height: 1px; background: var(--muted); margin: 20px 0 12px; opacity: 0.6; }
  .pitch .visit { font-size: 15px; margin: 0; }
  .pitch .visit a { color: var(--red); font-weight: 600; text-decoration: none; }
</style>
</head>
<body>
  <section class="card card-front">
    <div class="brand">
      <span class="brand-name">Birch Pin Links</span>
      <span class="brand-tagline">Indoor Golf Training. Open Around The Clock.</span>
    </div>
    <div class="contact">
      <h1 class="person-name">Daniel Carter</h1>
      <div class="person-role">Managing Director</div>
      <div class="rule"></div>
      <p>555-210-3388<br>www.birchpinlinks.com</p>
      <div class="rule"></div>
      <p>1480 Meadow Ridge Rd. Unit B4<br>Fairview, OH 45000</p>
    </div>
  </section>

  <section class="card card-back">
    <div class="pattern-field" role="img" aria-label="Faint repeating decorative pattern"></div>
    <div class="pitch">
      <h2>ELEVATOR PITCH</h2>
      <p>We work with serious golfers and those that want to be serious golfers… to make you better, faster at all phases of the game…</p>
      <p>We use the same state-of-the-art technology as professional golfers… which produces data sets that shows your improvement in real time.</p>
      <p>Our facility is available 24/7 to our members which allows you to improve on your time.</p>
      <div class="rule"></div>
      <p class="visit">Visit <a href="#">www.birchpinlinks.com</a> for more details.</p>
    </div>
  </section>
</body>
</html>
```